brightwell - Property Management DL Card

I am after a savvy designer to cut through junk mail! so many real estate agents use flyers to promote themselves and their business and usually sales. We are a property management firm (residential) and we want to represent landlords that have existing investment properties and need a quality agent to represent them. Can you help?
DL size, will be printed and delivered to mailboxes. For a look at our website go to www.brightwellrs.com.au. Keep it simple and clutter free.
it is to be double sided - with one side to be simple and clear - just our website, logo and telephone number on the back.
attached is our logo and our telephone number is 1300 48 92 16
the above are 2 essential elements to be included + our email address: admin@brightwellrs.com.au
also attached are our transparent price list

Target Market(s)
property investors,
people that manage properties themselves
Industry/Entity Type
Property Management
- arial
Look and feel

```html
<!DOCTYPE html>
<html lang="en">
<head>
<meta charset="utf-8">
<title>brightwell – Property Management DL Card</title>
<link rel="stylesheet" href="https://fonts.googleapis.com/css2?family=Open+Sans:wght@300;400&display=swap">
<style>
  :root {
    --page-bg: #d9d9d9;
    --card-black: #000000;
    --panel-black: #0b0b0b;
    --band-beige: #ded5b6;
    --band-red: #c33f27;
    --text-white: #ffffff;
    --text-soft: #e7c7bd;
    --phone-red: #d0402b;
    --divider: #9a9a9a;
  }
  * { box-sizing: border-box; margin: 0; padding: 0; }
  html, body {
    width: 1200px; height: 1200px; overflow: hidden;
    background: var(--page-bg);
    font-family: "Open Sans", Arial, sans-serif;
  }
  .card {
    position: absolute; left: 120px; width: 1000px; height: 500px;
    overflow: hidden;
  }
  .card--front { top: 57px; background: var(--band-beige); }
  .card--back { top: 637px; background: var(--card-black); }

  .front__photo {
    position: absolute; left: 0; top: 65px; width: 718px; height: 361px;
    background:
      radial-gradient(ellipse at 78% 30%, rgba(230,200,150,.55), transparent 45%),
      radial-gradient(ellipse at 55% 75%, rgba(40,30,25,.7), transparent 55%),
      linear-gradient(90deg, #6d6963 0%, #4a3a30 18%, #5e4a3b 40%, #8a7560 62%, #c9b79a 80%, #7a6a58 100%);
  }
  .front__panel {
    position: absolute; left: 718px; top: 65px; width: 282px; height: 361px;
    background: var(--panel-black);
  }
  .brand-name {
    color: var(--text-white); font-weight: 300; letter-spacing: .5px;
    line-height: 1;
  }
  .front__panel .brand-name {
    position: absolute; left: 0; right: 0; top: 160px;
    text-align: center; font-size: 38px;
  }
  .front__band {
    position: absolute; left: 0; top: 426px; width: 1000px; height: 74px;
    background: var(--band-red);
  }
  .band__tagline {
    position: absolute; left: 52px; top: 22px;
    color: var(--text-soft); font-size: 21px; font-weight: 400;
  }
  .band__divider {
    position: absolute; left: 423px; top: 17px; width: 1px; height: 38px;
    background: var(--text-soft);
  }
  .band__list {
    position: absolute; top: 15px; list-style: none;
    color: var(--text-white); font-size: 15.5px; line-height: 21px;
  }
  .band__list li::before { content: "•"; margin-right: 7px; }
  .band__list--a { left: 448px; }
  .band__list--b { left: 714px; }

  .card--back .brand-name {
    position: absolute; left: 54px; top: 50px; font-size: 42px;
  }
  .contact {
    position: absolute; left: 557px; top: 381px;
    border-left: 2px solid var(--divider); padding-left: 21px;
    font-size: 17.5px; line-height: 24.5px; color: var(--text-white);
    letter-spacing: .3px;
  }
  .contact__phone { color: var(--phone-red); }
</style>
</head>
<body>
  <section class="card card--front">
    <div class="front__photo" role="img" aria-label="Photograph of a modern dark-wood kitchen with stainless steel appliances, island bench and dining area"></div>
    <div class="front__panel">
      <p class="brand-name">brightwell</p>
    </div>
    <div class="front__band">
      <p class="band__tagline">Property Management specialists</p>
      <span class="band__divider"></span>
      <ul class="band__list band__list--a">
        <li>Excellent communication</li>
        <li>Minimal vacancy</li>
      </ul>
      <ul class="band__list band__list--b">
        <li>No hidden extras</li>
        <li>The best rent return</li>
      </ul>
    </div>
  </section>

  <section class="card card--back">
    <p class="brand-name">brightwell</p>
    <address class="contact" style="font-style:normal">
      <p class="contact__phone">1300 48 92 16</p>
      <p>PO Box B527, Parramatta NSW, 2124</p>
      <p>admin@brightwellrs.com.au</p>
    </address>
  </section>
</body>
</html>
```